Business Card Design Project - 2 sided

We need a business card design for a card having one business on each side (ie. two businesses on one card). Would like a design that incorporates logo, tagline and normal fields (name, position, address, phone).

Would also like an allowance for small font text along the bottom (text to be determined, but less than 50 characters).

NB. Attached logo for Harbor Quill has two variations - either can be used.

www.harborquill-example.com / www.velmaro-example.com

```html
<!DOCTYPE html>
<html lang="en">
<head>
<meta charset="utf-8">
<title>Harbor Quill / Velmaro – Business Card</title>
<link rel="stylesheet" href="https://fonts.googleapis.com/css2?family=Cabin:wght@400;600;700&family=Cabin+Condensed:wght@600&display=swap">
<style>
  :root {
    --stage: #4a2a17;
    --paper: #ffffff;
    --green: #8cc63f;
    --navy: #27215f;
    --navy-ink: #2e2a6b;
    --sky: #3789c6;
    --sky-ink: #2f8ac5;
    --tagline: #333333;
    --tagline-bold: #3c3c3c;
    --light: #ffffff;
  }
  * { box-sizing: border-box; margin: 0; padding: 0; }
  html, body { width: 1200px; height: 412px; overflow: hidden; }
  body {
    position: relative;
    background: var(--stage);
    font-family: "Cabin", "Trebuchet MS", sans-serif;
  }
  .icon-defs { position: absolute; width: 0; height: 0; }

  .card {
    position: absolute;
    top: 65px;
    width: 498px;
    height: 284px;
    background: var(--paper);
    box-shadow: 0 4px 10px rgba(0,0,0,0.45);
    overflow: hidden;
  }
  .card--harbor { left: 74px; }
  .card--velmaro { left: 629px; }

  .brand {
    position: absolute;
    left: 0; right: 0;
    display: flex;
    justify-content: center;
    align-items: center;
    gap: 10px;
  }
  .brand__mark { border-radius: 50%; flex: none; }
  .brand__name { white-space: nowrap; line-height: 1; }

  .card--harbor .brand { top: 62px; }
  .card--harbor .brand__mark { width: 22px; height: 22px; background: var(--green); }
  .card--harbor .brand__name {
    font-size: 28px; font-weight: 400; color: var(--navy-ink); letter-spacing: 1px;
  }
  .card--harbor .tagline {
    top: 119px; font-size: 11.5px; color: var(--tagline);
  }

  .card--velmaro .brand { top: 36px; }
  .card--velmaro .brand__mark { width: 46px; height: 46px; background: var(--sky); }
  .card--velmaro .brand__name {
    font-size: 50px; font-weight: 600; color: var(--sky-ink);
  }
  .card--velmaro .tagline {
    top: 108px; font-family: "Cabin Condensed", "Arial Narrow", sans-serif;
    font-weight: 600; font-size: 18px; color: var(--tagline-bold);
  }

  .tagline {
    position: absolute; left: 0; right: 0; text-align: center; white-space: nowrap;
  }

  .name-band {
    position: absolute; top: 150px; left: 0; right: 0; height: 27px;
    background: var(--green);
    display: flex; justify-content: center; align-items: baseline;
    padding-top: 4px;
    color: var(--light);
  }
  .name-band__name { font-weight: 700; font-size: 16px; }
  .name-band__title { font-size: 12.5px; margin-left: 5px; }

  .contact {
    position: absolute; top: 180px; left: 0; right: 0; bottom: 0;
    color: var(--light);
    font-size: 13px;
    text-align: center;
    padding-top: 13px;
  }
  .card--harbor .contact { background: var(--navy); }
  .card--velmaro .contact { background: var(--sky); }

  .contact__line {
    display: flex; justify-content: center; align-items: center; gap: 8px;
    height: 21px; white-space: nowrap;
  }
  .contact__item { display: inline-flex; align-items: center; gap: 2px; }
  .contact__icon { width: 11px; height: 11px; fill: var(--light); }
  .contact__fine { font-size: 11px; letter-spacing: 0.2px; }
</style>
</head>
<body>

<svg class="icon-defs" aria-hidden="true">
  <symbol id="icon-phone" viewBox="0 0 12 12">
    <path d="M2.6 0.8 L4.4 2.8 L3.4 4.2 Q4.6 6.9 7.8 8.6 L9.2 7.6 L11.2 9.4 L9.8 11.2 Q4.6 10.8 0.8 2.2 Z"/>
  </symbol>
  <symbol id="icon-mobile" viewBox="0 0 12 12">
    <path d="M3 0.5 H9 V11.5 H3 Z M4 1.8 V8.6 H8 V1.8 Z M5.4 9.4 H6.6 V10.6 H5.4 Z" fill-rule="evenodd"/>
  </symbol>
  <symbol id="icon-fax" viewBox="0 0 12 12">
    <path d="M0.5 4.5 Q6 1.5 11.5 4.5 V6 H8.8 V4.8 H3.2 V6 H0.5 Z M2 6.8 H10 L11 11 H1 Z"/>
  </symbol>
  <symbol id="icon-mail" viewBox="0 0 12 12">
    <path d="M1 3 H11 V10 H1 Z M1.8 3.8 L6 7 L10.2 3.8" fill-rule="evenodd"/>
  </symbol>
  <symbol id="icon-globe" viewBox="0 0 12 12">
    <circle cx="6" cy="6" r="5"/>
  </symbol>
</svg>

<section class="card card--harbor" aria-label="Harbor Quill side">
  <div class="brand">
    <span class="brand__mark"></span>
    <span class="brand__name">Harbor Quill</span>
  </div>
  <p class="tagline">Website Translation and Localisation Specialist...</p>

  <div class="name-band">
    <span class="name-band__name">Your Name</span>
    <span class="name-band__title">/ Title</span>
  </div>

  <div class="contact">
    <p class="contact__line">
      <span class="contact__item"><svg class="contact__icon"><use href="#icon-phone"/></svg>123-456-7890</span>
      <span class="contact__item"><svg class="contact__icon"><use href="#icon-mobile"/></svg>123-456-7890</span>
      <span class="contact__item"><svg class="contact__icon"><use href="#icon-fax"/></svg>123-456-7890</span>
    </p>
    <p class="contact__line">
      <span class="contact__item"><svg class="contact__icon"><use href="#icon-mail"/></svg>name@website.com</span>
      <span class="contact__item"><svg class="contact__icon"><use href="#icon-globe"/></svg>www.harborquill-example.com</span>
    </p>
    <p class="contact__line">Complex name, Street name, City, State, zip code</p>
    <p class="contact__line contact__fine">xxxxxxxxxxxxxxxxxxxxxxxxxxxxxxxxxxxxxxxxxxxxxxxxxx</p>
  </div>
</section>

<section class="card card--velmaro" aria-label="Velmaro side">
  <div class="brand">
    <span class="brand__mark"></span>
    <span class="brand__name">Velmaro LLC</span>
  </div>
  <p class="tagline">Professional SEO Services</p>

  <div class="name-band">
    <span class="name-band__name">Your Name</span>
    <span class="name-band__title">/ Title</span>
  </div>

  <div class="contact">
    <p class="contact__line">
      <span class="contact__item"><svg class="contact__icon"><use href="#icon-phone"/></svg>123-456-7890</span>
      <span class="contact__item"><svg class="contact__icon"><use href="#icon-mobile"/></svg>123-456-7890</span>
      <span class="contact__item"><svg class="contact__icon"><use href="#icon-fax"/></svg>123-456-7890</span>
    </p>
    <p class="contact__line">
      <span class="contact__item"><svg class="contact__icon"><use href="#icon-mail"/></svg>name@website.com</span>
      <span class="contact__item"><svg class="contact__icon"><use href="#icon-globe"/></svg>www.velmaro-example.com</span>
    </p>
    <p class="contact__line">Complex name, Street name, City, State, zip code</p>
    <p class="contact__line contact__fine">xxxxxxxxxxxxxxxxxxxxxxxxxxxxxxxxxxxxxxxxxxxxxxxxxx</p>
  </div>
</section>

</body>
</html>
```